BildeVOLD buisnesscard

Hey :) I need a modern buisnesscard for my company BildeVOLD
It most have:
Dagligleder og Fotograf: Henrik Audun Strandvik

Mob: +4791264085
Epost: post@bildevold.example
Adresse: Kvernbakken9, 6040 Langevåg

Facbook and instagram logo with text BildeVOLD

BildeVOLD logo

It Company

```html
<!DOCTYPE html>
<html lang="no">
<head>
<meta charset="utf-8">
<title>BildeVOLD – visittkort</title>
<link rel="stylesheet" href="https://fonts.googleapis.com/css2?family=Open+Sans:wght@400;600;700&display=swap">
<style>
  :root {
    --backdrop: #4a4a4a;
    --card-white: #ffffff;
    --brand-blue: #2181b5;
    --brand-pink: #cd4386;
    --text-grey: #4d4d4d;
    --divider: #d6d6d6;
    --white: #ffffff;
  }
  * { box-sizing: border-box; margin: 0; padding: 0; }
  html, body { width: 1105px; height: 1200px; overflow: hidden; }
  body {
    background: var(--backdrop);
    font-family: "Open Sans", Arial, sans-serif;
    position: relative;
  }
  .card {
    position: absolute;
    left: 193px;
    width: 719px;
    height: 412px;
    overflow: hidden;
  }
  .card--front { top: 167px; background: var(--card-white); }
  .card--back { top: 623px; background: var(--brand-pink); }

  /* front */
  .brand-block {
    position: absolute;
    left: 0; top: 0;
    width: 356px; height: 383px;
    display: flex; flex-direction: column; align-items: center; justify-content: center;
    gap: 18px;
  }
  .brand-square {
    width: 64px; height: 64px;
    background: var(--brand-pink);
  }
  .brand-name {
    font-weight: 700;
    font-size: 44px;
    line-height: 1;
    color: var(--brand-blue);
    letter-spacing: -0.5px;
  }
  .divider {
    position: absolute;
    left: 356px; top: 102px;
    width: 1px; height: 221px;
    background: var(--divider);
  }
  .contact {
    position: absolute;
    left: 389px; top: 104px;
    color: var(--text-grey);
  }
  .contact__name {
    font-weight: 600;
    font-size: 25px;
    color: var(--brand-blue);
    line-height: 1.2;
  }
  .contact__role {
    font-size: 19px;
    color: var(--brand-pink);
    line-height: 1.3;
    margin-bottom: 14px;
  }
  .contact__address {
    font-size: 19px;
    line-height: 1.4;
    margin-bottom: 14px;
  }
  .contact__list { list-style: none; font-size: 18px; line-height: 1.6; }
  .contact__list li { display: flex; align-items: center; gap: 12px; }
  .contact__list svg { width: 18px; height: 18px; flex: none; fill: var(--brand-blue); }
  .stripe { position: absolute; left: 0; bottom: 0; width: 719px; height: 29px; }

  /* back */
  .back-name {
    position: absolute;
    left: 0; right: 0; top: 158px;
    text-align: center;
    font-weight: 700;
    font-size: 54px;
    line-height: 1.1;
    color: var(--white);
  }
  .social-row {
    position: absolute;
    left: 0; top: 233px;
    width: 719px; height: 34px;
  }
</style>
</head>
<body>
  <section class="card card--front" aria-label="Visittkort forside">
    <div class="brand-block">
      <div class="brand-square"></div>
      <div class="brand-name">BildeVOLD</div>
    </div>
    <div class="divider"></div>
    <div class="contact">
      <p class="contact__name">Henrik Audun Strandvik</p>
      <p class="contact__role">Dagligleder og Fotograf</p>
      <p class="contact__address">Kvernbakken9<br>6040 Langevåg</p>
      <ul class="contact__list">
        <li><svg viewBox="0 0 18 18"><path d="M5 1h8a1 1 0 0 1 1 1v14a1 1 0 0 1-1 1H5a1 1 0 0 1-1-1V2a1 1 0 0 1 1-1zm1 2v10h6V3zm3 11.2a.9.9 0 1 0 0 1.8.9.9 0 0 0 0-1.8z"/></svg>+4791264085</li>
        <li><svg viewBox="0 0 18 18"><path d="M1 4h16v10H1zm1.5 1.2v.4L9 10l6.5-4.4v-.4z"/></svg>post@bildevold.example</li>
        <li><svg viewBox="0 0 18 18"><circle cx="9" cy="9" r="7.5"/><path d="M3 7h12M3 11h12M9 1.5c-3 3.5-3 11.5 0 15M9 1.5c3 3.5 3 11.5 0 15" stroke="#fff" stroke-width="1" fill="none"/></svg>www.bildevold.example</li>
      </ul>
    </div>
    <svg class="stripe" viewBox="0 0 719 29" preserveAspectRatio="none">
      <polygon points="0,0 467,0 461,29 0,29" fill="var(--brand-blue)"/>
      <polygon points="474,0 719,0 719,29 468,29" fill="var(--brand-pink)"/>
    </svg>
  </section>

  <section class="card card--back" aria-label="Visittkort bakside">
    <p class="back-name">BildeVOLD</p>
    <svg class="social-row" viewBox="0 0 719 34">
      <line x1="218" y1="17" x2="334" y2="17" stroke="var(--white)" stroke-width="1.5" opacity="0.8"/>
      <circle cx="359.5" cy="17" r="15" fill="none" stroke="var(--white)" stroke-width="2"/>
      <line x1="385" y1="17" x2="505" y2="17" stroke="var(--white)" stroke-width="1.5" opacity="0.8"/>
    </svg>
  </section>
</body>
</html>
```